Verpackungen für Sekt/Champagner Flaschen
Zielgruppe
Dekoration für Hochzeiten. Tisch Dekoration für Hochzeiten. Zielgruppe alles was mit Hochzeiten zutun hat
Aufgabenstellung
Wir lassen gerade ein Tube/Dose herstellen, die als Umverpackung oder einfach Verpackung für Sekt/Champagne Flaschen dienen soll die dann auf die Tische für Hochzeit´s Deko kommt um die die Tisch Deko aufzubessern, statt einfach nur eine Sekt Flasche stehen zu haben. .Die Tube wird komplett in weiß sein und alles andere an Design soll in einem Gold sein. Mr&Mrs oder Just Married mit Herzen und alles was sonst dazu gehört, da lassen wir freie Hand.
Das Design soll Schlicht sein aber auch Luxuriös.
Durchmesser der Tube wird 8,5 cm haben und 34-35 cm sein.
Die Goldene Schrift und das Muster soll am Ende in einem Relief Lack auf der Tube erscheinen

```html
<!DOCTYPE html>
<html lang="en">
<head>
<meta charset="utf-8">
<title>Mr&amp;Mrs – Bottle Tube Band</title>
<link rel="stylesheet" href="https://fonts.googleapis.com/css2?family=Federo&display=swap">
<style>
  :root {
    --paper: #ffffff;
    --gold-band: #c9a171;
    --gold-type: #8f7351;
    --flourish-tone: #3a2f2b;
  }
  html, body {
    margin: 0;
    padding: 0;
    width: 1200px;
    height: 287px;
    overflow: hidden;
    background: var(--paper);
  }
  .band-design {
    position: relative;
    width: 1200px;
    height: 287px;
    background: var(--paper);
  }
  .rule-pair {
    position: absolute;
    top: 0;
    left: 0;
  }
  .flourish {
    position: absolute;
    width: 180px;
    height: 36px;
    border-radius: 18px;
    background: linear-gradient(90deg, rgba(58,47,43,0) 0%, rgba(58,47,43,0.55) 50%, rgba(58,47,43,0) 100%);
  }
  .flourish--left-top     { left: 101px; top: 98px; }
  .flourish--left-bottom  { left: 101px; top: 181px; }
  .flourish--right-top    { left: 857px; top: 98px; }
  .flourish--right-bottom { left: 857px; top: 181px; }
  .couple-title {
    position: absolute;
    left: 0;
    right: 0;
    top: 72px;
    margin: 0;
    text-align: center;
    font-family: "Federo", serif;
    font-weight: 400;
    font-size: 118px;
    line-height: 1;
    letter-spacing: -3px;
    color: var(--gold-type);
    transform: scaleX(0.82);
  }
</style>
</head>
<body>
  <div class="band-design">
    <svg class="rule-pair" width="1200" height="287" viewBox="0 0 1200 287" aria-hidden="true">
      <g fill="var(--gold-band)">
        <rect x="0" y="144" width="441" height="8"/>
        <rect x="0" y="160" width="441" height="8"/>
        <rect x="760" y="144" width="440" height="8"/>
        <rect x="760" y="160" width="440" height="8"/>
      </g>
    </svg>

    <div class="flourish flourish--left-top" role="img" aria-label="Dark calligraphic scroll flourish above the left gold rules"></div>
    <div class="flourish flourish--left-bottom" role="img" aria-label="Dark calligraphic scroll flourish below the left gold rules"></div>
    <div class="flourish flourish--right-top" role="img" aria-label="Dark calligraphic scroll flourish above the right gold rules"></div>
    <div class="flourish flourish--right-bottom" role="img" aria-label="Dark calligraphic scroll flourish below the right gold rules"></div>

    <h1 class="couple-title">Mr&amp;Mrs</h1>
  </div>
</body>
</html>
```